Design a calming beauty medical salon & spa website based in Hong Kong

We need help building an informational website for a beauty salon in Hong Kong. The local salon provides facials, massages, body and other slimming treatments in a relaxing environment. We offer some non-invasive medical treatments, such as botox. Having built the business on word of mouth, it is now time for us to launch a website to help market the business better. Website requirements:

-Must be responsive
-Use vibrant but clean colours. not too many, 1-2 colours
-Must be bilingual (switch between Chinese traditional and English)
-Our current website is host on a server, not using any particular platforms like wordpress

Pages:
1/ Homepage
2/ About us (incorporate gallery of salon photos and history of company)
3/ Promotions and latest deals (and leads them to sign up for more info, maybe pop-up small window when you click on a promotion)
4/ Treatment menus
4.1/Body treatments
4.2/ Face treatments
4.3/ Slimming treatments
5/ Showcasing products sold (no e-commerce functionality, just showing off products)
6/ Contact us (tel, address, map, opening hrs)

Footer - must haves include contact us info, privacy policy, terms & conditions, copyright blurb, join our company/employment page (with a form)

For information (comparable websites we like):
http://veltora.com/
http://pambrix.com.hk/tc/aboutpambrix/background.php#centerenvi
Attaching a very first draft concept for this website
Attaching pictures of the beauty salon
Attaching logo

Target Market(s)

Hong Kong based, Chinese, females, 30-50+ age. 90% female clients.

Industry/Entity Type

Beauty Salon

Number of Pages Required

5+ page

Font styles to use
Sans Serif

Colors
f9d9e8
fbd3d4
fee3d5
fbe7d2
fee18a
fbf289
ffffff

Requirements
Must have
• interactive elements on website, such as scrolling banner photo headers
• incorporate photos of website salon
• connect to facebook page

```html
<!DOCTYPE html>
<html lang="en">
<head>
<meta charset="utf-8">
<title>Serene Bloom – Promotions</title>
<link href="https://fonts.googleapis.com/css2?family=Signika:wght@300;400;600;700&display=swap" rel="stylesheet">
<style>
:root{
  --blush:#f0d3d1;
  --blush-deep:#dcb4b0;
  --rose:#c4948e;
  --plum:#6b1a7d;
  --ink:#111;
  --text:#2a2a2a;
  --white:#fff;
  --photo-spa-a:#3a2a2c;
  --photo-spa-b:#b0457f;
  --photo-face-a:#f7eee9;
  --photo-face-b:#eed3c6;
}
*{box-sizing:border-box;margin:0;padding:0}
html,body{width:1193px;height:1200px;overflow:hidden;background:var(--white)}
body{position:relative;font-family:"Signika",sans-serif;font-weight:300;color:var(--text)}
a{color:inherit;text-decoration:none}

/* header */
.top-tab{position:absolute;left:437px;top:0;width:756px;height:35px;background:var(--blush);border-bottom-left-radius:18px;box-shadow:0 2px 3px rgba(0,0,0,.25);display:flex;align-items:center;font-size:13px;font-weight:400;letter-spacing:1.3px;color:var(--ink)}
.top-tab span{display:flex;align-items:center;gap:7px}
.tab-email{position:absolute;left:63px}
.tab-social{position:absolute;left:278px}
.tab-lang{position:absolute;right:87px}
.tab-sep{position:absolute;top:9px;width:1px;height:17px;background:#fff}
.brand{position:absolute;left:86px;top:36px;display:flex;align-items:center;gap:10px;color:var(--plum);font-size:31px;font-weight:600}
.brand .mark{width:44px;height:44px;border-radius:50%;background:var(--plum)}
.contact-line{position:absolute;top:60px;font-size:15.5px;letter-spacing:1.2px;line-height:21px;color:var(--ink)}
.tel{left:518px}
.hours{left:788px}
.hdr-icon{position:absolute;top:62px}

.nav{position:absolute;left:0;top:125px;width:1193px;height:35px;background:var(--blush)}
.nav a{position:absolute;top:0;height:35px;line-height:35px;font-size:16px;letter-spacing:1.6px;color:var(--ink)}
.nav a.active{background:var(--blush-deep);padding:0 26px}

/* promotions */
.page-title{position:absolute;left:0;width:1193px;top:212px;text-align:center;font-size:33px;font-weight:700;letter-spacing:3px;color:var(--ink)}
.divider{position:absolute;left:546px;top:266px;width:100px;height:20px}
.photo{position:absolute;top:310px;height:292px}
.photo-spa{left:86px;width:497px;background:radial-gradient(circle at 55% 55%,var(--photo-spa-b) 0%,#7a3a5c 35%,var(--photo-spa-a) 75%)}
.photo-face{left:609px;width:496px;background:radial-gradient(ellipse at 50% 45%,var(--photo-face-b) 0%,var(--photo-face-a) 70%,#fff 100%);border:1px solid #e6e6e6}
.promo{position:absolute;top:622px;text-align:center}
.promo-left{left:86px;width:497px}
.promo-right{left:609px;width:496px}
.promo h2{font-size:22px;font-weight:400;letter-spacing:7px;color:var(--rose)}
.promo p{margin-top:9px;font-size:16px;letter-spacing:1.3px;line-height:23px;color:var(--ink)}
.btn{position:absolute;top:713px;width:163px;height:44px;line-height:44px;text-align:center;background:var(--rose);color:#fff;border-top-left-radius:14px;border-bottom-right-radius:14px;font-size:16px;font-weight:600;letter-spacing:1.5px}

/* footer */
.footer{position:absolute;left:0;top:819px;width:1193px;height:353px;background:var(--blush)}
.footer h3{position:absolute;font-size:27px;font-weight:700;letter-spacing:2px;color:var(--ink)}
.info-list{position:absolute;left:86px;top:100px;list-style:none;font-size:14px;line-height:22.7px;letter-spacing:.4px}
.info-list li{position:relative;padding-left:35px;margin-bottom:10px}
.info-list .dot{position:absolute;left:0;top:0;width:24px;height:24px;border-radius:50%;background:var(--ink);display:flex;align-items:center;justify-content:center}
.foot-brand{position:absolute;left:463px;top:60px;display:flex;align-items:center;gap:10px;color:var(--plum);font-size:31px;font-weight:600}
.foot-brand .mark{width:44px;height:44px;border-radius:50%;background:var(--plum)}
.about-blurb{position:absolute;left:463px;top:165px;width:280px;font-size:14px;line-height:21px;letter-spacing:.3px}
.links{position:absolute;left:872px;top:92px;list-style:none;font-size:14px;line-height:22.7px;letter-spacing:.6px}
.legal{position:absolute;left:0;top:1172px;width:1193px;height:28px;background:var(--ink);color:#fff;text-align:center;font-size:14px;line-height:28px;letter-spacing:.3px}
</style>
</head>
<body>

<header>
  <div class="top-tab">
    <span class="tab-email"><svg width="15" height="11" viewBox="0 0 15 11"><rect width="15" height="11" rx="1" fill="#111"/><path d="M1 1l6.5 5 6.5-5" stroke="#f0d3d1" stroke-width="1.4" fill="none"/></svg>Email Us</span>
    <i class="tab-sep" style="left:218px"></i>
    <span class="tab-social"><svg width="12" height="12"><rect width="12" height="12" rx="2" fill="#111"/></svg>Connect on Social Media</span>
    <i class="tab-sep" style="left:527px"></i>
    <span class="tab-lang">ENG &nbsp;| &nbsp;CN</span>
  </div>

  <a class="brand" href="#"><span class="mark"></span>Serene Bloom</a>

  <svg class="hdr-icon" style="left:466px" width="36" height="36" viewBox="0 0 36 36"><path d="M8 4c-3 2-4 6-2 10 3 7 9 14 16 17 4 2 7 0 9-3l-5-5-4 3c-4-2-8-6-10-10l3-4-5-6z" fill="#c4948e"/><path d="M22 6a9 9 0 0 1 8 8M22 1a14 14 0 0 1 13 13" stroke="#c4948e" stroke-width="2" fill="none"/></svg>
  <div class="contact-line tel">TEL: 23456789<br>WHATSAPP: 6123 4567</div>

  <svg class="hdr-icon" style="left:740px" width="36" height="36" viewBox="0 0 36 36"><rect x="2" y="5" width="25" height="24" rx="2" fill="none" stroke="#c4948e" stroke-width="2"/><path d="M2 11h25M8 2v6M21 2v6" stroke="#c4948e" stroke-width="2"/><g fill="#c4948e"><rect x="6" y="15" width="3" height="3"/><rect x="12" y="15" width="3" height="3"/><rect x="18" y="15" width="3" height="3"/><rect x="6" y="21" width="3" height="3"/><rect x="12" y="21" width="3" height="3"/></g><circle cx="27" cy="27" r="7" fill="#fff" stroke="#c4948e" stroke-width="2"/><path d="M27 23v4h3" stroke="#c4948e" stroke-width="1.6" fill="none"/></svg>
  <div class="contact-line hours">MON TO FRI: 10.30 AM TO 9.30PM<br>SAT AND HOLIDAY: 10.30 AM TO 7.30PM</div>

  <nav class="nav">
    <a href="#" style="left:112px">HOME</a>
    <a href="#" style="left:241px">ABOUT US</a>
    <a href="#" class="active" style="left:384px">PROMOTIONS</a>
    <a href="#" style="left:609px">TREATMENT</a>
    <a href="#" style="left:799px">PRODUCTS</a>
    <a href="#" style="left:974px">CONTACT US</a>
  </nav>
</header>

<main>
  <h1 class="page-title">PROMOTIONS</h1>
  <svg class="divider" viewBox="0 0 100 20"><path d="M0 11h30M70 11h30" stroke="#c4948e" stroke-width="1"/><circle cx="50" cy="10" r="8" fill="none" stroke="#c4948e" stroke-width="1.5"/></svg>

  <div class="photo photo-spa" role="img" aria-label="Foot soaking in a stone bowl with orchid flowers beside a rolled towel"></div>
  <div class="photo photo-face" role="img" aria-label="Close-up facial skincare photo"></div>

  <section class="promo promo-left">
    <h2>HOT STONE MASSAGE</h2>
    <p>10% OFF FIRST TIMERS</p>
  </section>
  <a class="btn" href="#" style="left:253px">FIND OUT MORE</a>

  <section class="promo promo-right">
    <h2>TREATMENT PACKAGE</h2>
    <p>GET DISCOUNTS FOR FREE TREATMENT WHEN YOU<br>PURCHASE 3 OR MORE OF THE SAME TREATMENT.</p>
  </section>
  <a class="btn" href="#" style="left:775px">FIND OUT MORE</a>
</main>

<footer class="footer">
  <h3 style="left:86px;top:56px">CONTACT INFO</h3>
  <ul class="info-list">
    <li><span class="dot"><svg width="10" height="14" viewBox="0 0 10 14"><path d="M5 0a5 5 0 0 0-5 5c0 4 5 9 5 9s5-5 5-9a5 5 0 0 0-5-5z" fill="#fff"/><circle cx="5" cy="5" r="2" fill="#111"/></svg></span>12/F., Jade Lotus Centre,<br>21-23 Orchid Road, Tsim Sha<br>Tsui, Kowloon, Hong Kong</li>
    <li><span class="dot"><svg width="12" height="12" viewBox="0 0 12 12"><path d="M2 1c-1 1-1 3 0 5 1 2 3 4 5 5 2 1 3 0 4-1L9 8 7.5 9C6 8 4 6 3 4.5L4 3z" fill="#fff"/></svg></span>2345 6789</li>
    <li><span class="dot"><svg width="12" height="12" viewBox="0 0 12 12"><path d="M2 1c-1 1-1 3 0 5 1 2 3 4 5 5 2 1 3 0 4-1L9 8 7.5 9C6 8 4 6 3 4.5L4 3z" fill="#fff"/></svg></span>6123 4567</li>
    <li><span class="dot"><svg width="12" height="9" viewBox="0 0 12 9"><rect width="12" height="9" rx="1" fill="#fff"/><path d="M1 1l5 4 5-4" stroke="#111" stroke-width="1.2" fill="none"/></svg></span>hello@serenebloom.com.hk</li>
    <li><span class="dot"></span>Connect on Social Media</li>
  </ul>

  <a class="foot-brand" href="#"><span class="mark"></span>Serene Bloom</a>
  <p class="about-blurb">Our professional consultant team provides exceptional knowledge and service, for tailor made treatments, customized to meet your specific needs.</p>

  <h3 style="left:872px;top:56px">LINKS</h3>
  <ul class="links">
    <li>Home</li><li>About Us</li><li>Promotion</li><li>Body Treatments</li><li>Facial Treatments</li><li>Slimming Treatments</li><li>Products</li><li>Contact Us</li><li>Join Us</li>
  </ul>
</footer>
<div class="legal">Copyright © 2018 Serene Bloom HK Ltd. All Rights Reserved. Privacy Policy | Terms of Use</div>

</body>
</html>
```